ELsewhen website redesign to provide information about experiential workshops, film work and other

We need a redesign of our website elsewhen.org. We conduct experiential workshops of discovery and transformation for individuals and organizations. We need the website to reflect the full extent of ELsewhen programs, and be an information hub for ELsewhen workshops and communities as they develop.

The attached documents contain information about the organization - it's brandbook, copy for web pages, a website layout and a couple of images.

The site is for individuals and companies looking to promote and be change to make a difference. It should be warm, welcoming, and create excitement around the concepts and the ability to discover a new way of being in the world. We are about creating communities around the globe who will embody play, freedom, curiosity and expanded possibilities. We are creating a space for this to happen, both physically (workshops) and online.

We will be on either a SquareSpace, but mos tlikely a Weebly plaform.

Please look at the current site at www.elsewhen.org

Target Market(s)

Initially, are target market will be baby boomers, but will expand to include millennials and students.

Coding

Coded - Design and coding required

Number of Pages Required

5+ page

Requirements
Must have
• The colors, logo and fonts from the brand book.
Nice to have
• Complimentary use of brand colors to create an attractive presentation and energy

```html
<!DOCTYPE html>
<html lang="en">
<head>
<meta charset="utf-8">
<title>ELsewhen — Experiential Workshops</title>
<link href="https://fonts.googleapis.com/css2?family=Montserrat:wght@400;500;600;700;800&family=Open+Sans:wght@400;600&display=swap" rel="stylesheet">
<style>
:root{
  --ink:#1a1a1a;
  --charcoal:#262626;
  --grey-dark:#3a3a3a;
  --grey-mid:#8a8a8a;
  --grey-light:#d9d9d9;
  --panel:#e6e6e6;
  --paper:#ffffff;
  --rose:#c98888;
  --gold:#f2b53a;
  --text:#555555;
}
*{box-sizing:border-box;margin:0;padding:0}
html,body{width:1200px;height:3064px;overflow:hidden;background:var(--paper)}
body{position:relative;font-family:"Open Sans",Arial,sans-serif;color:var(--text)}
.abs{position:absolute}
h1,h2,h3,h4,.brand,.nav a,.btn,.label{font-family:"Montserrat",Helvetica,sans-serif}

/* nav */
.site-nav{left:0;top:0;width:1200px;height:64px;background:var(--ink);display:flex;align-items:center;padding:0 40px}
.brand{color:#fff;font-weight:800;font-size:26px;letter-spacing:1px}
.nav{margin-left:auto;display:flex;height:64px}
.nav a{color:#fff;text-decoration:none;font-size:11px;font-weight:600;letter-spacing:1px;text-transform:uppercase;display:flex;align-items:center;padding:0 14px}
.nav a.active{background:var(--rose)}

/* hero */
.hero-left{left:0;top:64px;width:600px;height:716px;background:linear-gradient(160deg,#5a5a5a 0%,#2a2a2a 45%,#111 100%)}
.hero-right{left:600px;top:64px;width:600px;height:716px;background:linear-gradient(120deg,#f2f2f2 0%,#c9c9c9 50%,#8c8c8c 100%)}
.hero-band{left:560px;top:72px;width:90px;height:740px;background:var(--ink);display:flex;flex-direction:column;align-items:center;justify-content:center;gap:14px}
.hero-band span{color:#fff;font-family:"Montserrat",sans-serif;font-weight:800;font-size:40px;line-height:1}
.label{font-size:13px;font-weight:700}
.hero-title{font-size:38px;font-weight:800;line-height:1.12;text-transform:uppercase}
.btn{display:inline-block;border:2px solid currentColor;border-radius:20px;padding:9px 20px;font-size:11px;font-weight:700;text-decoration:none}
.hero-copy-left{left:80px;top:292px;width:380px;color:#fff}
.hero-copy-left .hero-title{color:var(--gold);margin:14px 0 44px}
.hero-copy-left .btn{color:#fff}
.hero-copy-right{left:680px;top:292px;width:420px;color:var(--ink)}
.hero-copy-right .hero-title{margin:14px 0 44px}
.hero-copy-right .btn{color:var(--ink)}

/* guide lines */
.guide{background:#999;width:1px}

/* discover */
.photo{display:block}
.discover-photo{left:0;top:800px;width:760px;height:360px;background:linear-gradient(135deg,#9a9a9a,#4a4a4a 60%,#2a2a2a)}
.discover-card{left:540px;top:896px;width:548px;height:432px;background:#fff;box-shadow:0 0 0 1px #bbb;padding:46px 40px}
.discover-card h2{font-size:34px;font-weight:700;color:var(--ink);line-height:1.2;margin:14px 0 34px}
.bullets{list-style:none}
.bullets li{font-family:"Montserrat",sans-serif;font-size:11px;font-weight:600;color:var(--ink);letter-spacing:.5px;margin-bottom:12px;padding-left:18px;position:relative}
.bullets li::before{content:"";position:absolute;left:0;top:4px;width:5px;height:5px;background:var(--ink)}

/* what we do */
.section-tag{left:40px;top:1400px;width:60px;height:180px;display:flex;align-items:center;justify-content:center}
.section-tag h3{transform:rotate(-90deg);white-space:nowrap;font-size:32px;font-weight:700;color:var(--ink)}
.intro{left:272px;top:1362px;width:848px;font-size:13px;line-height:1.75}
.values{left:272px;top:1488px;width:848px;display:flex;gap:12px}
.value{flex:1;height:224px;background:#fff;box-shadow:0 2px 8px rgba(0,0,0,.12);text-align:center;padding:20px 12px}
.value-mark{display:block;width:56px;height:56px;margin:4px auto 0;background:var(--grey-light);border-radius:4px}
.value h4{font-size:13px;font-weight:700;color:var(--ink);margin:14px 0 8px;white-space:nowrap}
.value p{font-size:11px;line-height:1.5;color:#777}
.value .more{display:block;margin-top:12px;font-family:"Montserrat",sans-serif;font-size:11px;font-weight:700;color:var(--ink)}
.tagline{left:272px;top:1732px;width:848px;text-align:center;font-family:"Montserrat",sans-serif;font-size:14px;font-weight:600;letter-spacing:3px;white-space:nowrap;color:var(--grey-dark)}

/* vision */
.vision-head{left:200px;top:1840px;width:220px;text-align:right}
.vision-head h2{font-size:46px;font-weight:600;color:var(--ink)}
.vision-head p{font-family:"Montserrat",sans-serif;font-size:25px;font-weight:600;color:var(--rose);line-height:1.25;margin-top:16px}
.vision-rule{left:448px;top:1848px;width:1px;height:170px;background:#999}
.vision-text{left:480px;top:1848px;width:640px;font-size:13px;line-height:1.75}
.vision-btn{left:480px;top:2010px;color:var(--ink)}

/* community */
.community-photo{left:0;top:2140px;width:560px;height:420px;background:linear-gradient(160deg,#7a7a7a,#3a3a3a 55%,#1e1e1e)}
.community-panel{left:380px;top:2192px;width:820px;height:508px;background:linear-gradient(135deg,#f0f0f0,#d8d8d8)}
.community-copy{left:512px;top:2250px;width:600px}
.community-copy h2{display:flex;gap:60px;font-size:22px;font-weight:700;color:var(--ink);margin:14px 0 10px;padding-bottom:10px;border-bottom:1px solid #bbb}
.community-copy p{font-size:13px;line-height:1.75;margin-top:20px}
.community-copy .btn{margin-top:44px;color:var(--ink)}

/* footer */
.footer{left:0;top:2776px;width:1200px;height:288px;background:var(--charcoal);color:#cfcfcf}
.footer-links{left:160px;top:2806px;display:flex;gap:28px;font-size:12px}
.footer-links a{color:#cfcfcf;text-decoration:none}
.social{left:820px;top:2796px;display:flex;align-items:center;gap:12px;font-family:"Montserrat",sans-serif;font-size:11px;font-weight:700;color:#fff;letter-spacing:1px}
.social i{display:block;width:32px;height:32px;border:2px solid #bbb;border-radius:50%}
.footer-rule{left:160px;top:2856px;width:880px;height:1px;background:#555}
.footer-brand{left:160px;top:2930px;font-size:36px;color:#fff}
.footer-col h4{font-size:20px;font-weight:700;color:#fff;margin-bottom:14px}
.footer-col p{font-size:12px;line-height:2;color:#bbb}
.contact{left:480px;top:2876px}
.newsletter{left:700px;top:2876px;width:340px}
.newsletter .field{display:flex;height:40px;margin-top:10px}
.newsletter .field span{flex:1;border-bottom:1px solid #888;font-size:12px;color:#bbb;padding-top:14px}
.newsletter .field b{width:110px;background:var(--gold);color:var(--ink);font-family:"Montserrat",sans-serif;font-size:11px;display:flex;align-items:center;justify-content:center;letter-spacing:1px}
.copyright{left:160px;top:3032px;font-size:11px;color:#999}
.policy{left:960px;top:3032px;font-size:11px;color:#999}
</style>
</head>
<body>

<header class="site-nav abs">
  <div class="brand">ELsewhen</div>
  <nav class="nav">
    <a class="active">Home</a><a>Workshop</a><a>ELsewhen Projects</a><a>Film</a><a>Store &amp; Resources</a><a>Community</a><a>Contact</a>
  </nav>
</header>

<div class="hero-left abs photo" role="img" aria-label="Black and white photo of workshop participants gathered in a room"></div>
<div class="hero-right abs"></div>
<div class="hero-band abs" aria-label="ELsewhen"><span>E</span><span>L</span><span>S</span><span>E</span><span>W</span><span>H</span><span>E</span><span>N</span></div>

<div class="hero-copy-left abs">
  <div class="label">ELsewhen</div>
  <h1 class="hero-title">What world do we want to live in?</h1>
  <a class="btn">Learn More</a>
</div>
<div class="hero-copy-right abs">
  <div class="label">ELsewhen</div>
  <h1 class="hero-title">What kind of life do you want to create?</h1>
  <a class="btn">Learn More</a>
</div>

<div class="guide abs" style="left:184px;top:740px;height:360px"></div>
<div class="guide abs" style="left:184px;top:1330px;height:420px"></div>

<div class="discover-photo abs photo" role="img" aria-label="Black and white photo of a workshop circle in a wooden hall"></div>
<section class="discover-card abs">
  <div class="label" style="color:var(--ink)">ELsewhen</div>
  <h2>Discover an Opportunity to Live a More Dynamic and Meaningful Life</h2>
  <ul class="bullets">
    <li>WHOLE BRAINED</li>
    <li>CREATES OPPORTUNITIES FOR CONNECTING</li>
    <li>SUPPORTS CONSCIOUS EVOLUTION</li>
    <li>DEEPENS EXPERIENCE OF LIFE</li>
    <li>PROVIDES OPPORTUNITIES FOR COLLABORATION AND CREATION</li>
  </ul>
</section>

<div class="section-tag abs"><h3>What We Do</h3></div>
<p class="intro abs">ELsewhen Life is a workshop designed to re-engage you with life. Through interactive exercises and experiential exploration, you are taken on a journey that ultimately assists you in questioning the way it is. Together we see what's possible in a world that fits who you are, and relationships as well as a path to transforming the story of your life.</p>

<div class="values abs">
  <div class="value">
    <span class="value-mark" role="img" aria-label="Value symbol for curiosity"></span>
    <h4>Curiosity</h4><p>Ask questions and follow the spark</p><span class="more">Learn More</span>
  </div>
  <div class="value">
    <span class="value-mark" role="img" aria-label="Value symbol for openness"></span>
    <h4>Openness</h4><p>Meet each moment with a wide view</p><span class="more">Learn More</span>
  </div>
  <div class="value">
    <span class="value-mark" role="img" aria-label="Value symbol for owning your creation"></span>
    <h4>Own Your Creation</h4><p>Shape the story you choose to live</p><span class="more">Learn More</span>
  </div>
  <div class="value">
    <span class="value-mark" role="img" aria-label="Value symbol for emboldening"></span>
    <h4>Embolden</h4><p>Take bold steps toward what matters</p><span class="more">Learn More</span>
  </div>
  <div class="value">
    <span class="value-mark" role="img" aria-label="Value symbol for manifesting"></span>
    <h4>Manifest</h4><p>Bring intention into the world</p><span class="more">Learn More</span>
  </div>
</div>

<p class="tagline abs">ELSEWHEN LIFE IS A 2-3 DAY WORKSHOP EXPERIENCED IN 3 MOVEMENTS</p>

<div class="vision-head abs">
  <h2>Vision</h2>
  <p>We take responsibility for the world we are manifesting</p>
</div>
<div class="vision-rule abs"></div>
<div class="vision-text abs">
  <p>ELsewhen's vision is a world where people and communities are inspired and freed from the stories that no longer serve us. We believe that an invitation to reimagine how we engage with life brings a new era of curiosity, care and connection.</p>
  <p style="margin-top:12px">Through inspiration, exploration, reflection and collaboration, we take responsibility for the world we are manifesting, so that each moment we create new possibilities for ourselves and the world.</p>
</div>
<a class="btn abs vision-btn">Learn More</a>

<div class="community-photo abs photo" role="img" aria-label="Black and white photo of a group gathered at a community event"></div>
<div class="community-panel abs"></div>
<section class="community-copy abs">
  <div class="label" style="color:var(--ink)">ELsewhen</div>
  <h2><span>Stirring the Calm</span><span>In Your Community</span></h2>
  <p>The Stirring the Calm workshop — an extension of our film work of the same spirit — is an experiential process to transform participants into believers of the values they hold for themselves, to embrace their relationships with others, and to change the local scenario in which they work, live and educate, for the better.</p>
  <p>This workshop transforms challenges, as we've understood that ourselves are the authority to build all our stories and all of its values, and to decide what values will give us for a more humane, just and peaceful world, for all. It all starts with our willingness to stir the "calm" of the status quo.</p>
  <a class="btn">Learn More</a>
</section>

<footer class="footer abs"></footer>
<nav class="footer-links abs"><a>Home</a><a>About Us</a><a>Community</a><a>Catalog</a><a>Contact Us</a></nav>
<div class="social abs">CONNECT WITH US <i></i><i></i><i></i></div>
<div class="footer-rule abs"></div>
<div class="brand footer-brand abs">ELsewhen</div>
<div class="footer-col contact abs">
  <h4>Contact Us</h4>
  <p>(555) 014-2290</p>
  <p>info@elsewhen.org</p>
</div>
<div class="footer-col newsletter abs">
  <h4>Newsletter</h4>
  <p>Sign up for new updates</p>
  <div class="field"><span>Your email address</span><b>SUBSCRIBE</b></div>
</div>
<div class="copyright abs">© Copyright 2024 ELsewhen. All Rights Reserved.</div>
<div class="policy abs">Privacy Policy</div>

</body>
</html>
```